Income Tax Flyer - Updates Needed

Just need to update this flyer design and give it a new look. We would like to keep all the same wording but make it stand out a little more. Our selling point is the "Same Day Tax Advance up to $6,000"

Lending, Small Loans, Tax Services, Title Loans, Personal Loans

```html
<!DOCTYPE html>
<html lang="en">
<head>
<meta charset="UTF-8">
<title>Same Day Tax Advance – Harbrook Financial Group</title>
<link rel="stylesheet" href="https://fonts.googleapis.com/css2?family=Oswald:wght@400;500;600&display=swap">
<style>
  :root {
    --green: #0e5130;
    --red: #c41f2a;
    --white: #ffffff;
    --grey: #86868b;
    --photo-a: #e9e4df;
    --photo-b: #2a2a2e;
  }
  * { margin: 0; padding: 0; box-sizing: border-box; }
  html, body { width: 848px; height: 1200px; overflow: hidden; background: var(--white); }
  body { font-family: "Oswald", "Arial Narrow", sans-serif; }
  .flyer { position: relative; width: 848px; height: 1200px; overflow: hidden; background: var(--white); }

  .panel-top { position: absolute; left: 0; top: 0; width: 433px; height: 664px; background: var(--green); }
  .panel-bottom { position: absolute; left: 0; top: 850px; width: 433px; height: 350px; background: var(--green); }
  .band { position: absolute; left: 0; top: 664px; width: 848px; height: 186px; background: var(--red); }

  .photo { position: absolute; left: 350px; top: 178px; width: 498px; height: 486px;
    background: radial-gradient(ellipse at 62% 40%, var(--photo-a) 0 30%, #6b5a4f 46%, var(--photo-b) 70%);
    border-radius: 180px 180px 0 0; }

  .headline { position: absolute; left: 0; top: 0; width: 433px; height: 664px; color: var(--white); text-align: center; z-index: 2; }
  .headline span { position: absolute; left: 0; width: 433px; display: block; white-space: nowrap; font-weight: 500; line-height: 1; transform-origin: 50% 50%; }
  .hl-sameday { top: 63px; font-size: 81px; transform: scaleX(0.91); }
  .hl-tax { top: 120px; font-size: 222px; transform: scaleX(0.89); }
  .hl-advance { top: 313px; font-size: 84px; transform: scaleX(0.9); }
  .hl-upto { top: 387px; font-size: 84px; transform: scaleX(0.9); }
  .hl-amount { top: 462px; font-size: 173px; transform: scaleX(0.82); }

  .brand { position: absolute; left: 510px; top: 72px; width: 250px; display: flex; align-items: center; gap: 10px; }
  .brand-dot { width: 22px; height: 22px; border-radius: 50%; background: var(--red); flex: none; }
  .brand-name { color: var(--green); font-weight: 500; font-size: 30px; line-height: 1.1; }

  .band-lead { position: absolute; left: 0; top: 676px; width: 848px; text-align: center; color: var(--white); font-size: 40px; font-weight: 400; line-height: 1.1; letter-spacing: -0.5px; }
  .band-title { position: absolute; left: 0; top: 716px; width: 848px; text-align: center; color: var(--white); font-size: 54px; font-weight: 600; line-height: 1.1; letter-spacing: -0.5px; }

  .feature { position: absolute; top: 800px; width: 213px; height: 179px; background: var(--white); border: 1px solid var(--green); text-align: center; }
  .feature-1 { left: 24px; } .feature-2 { left: 316px; } .feature-3 { left: 607px; }
  .feature svg { position: absolute; left: 50%; transform: translateX(-50%); top: 14px; }
  .feature p { position: absolute; left: 0; top: 84px; width: 100%; color: var(--grey); font-size: 36px; font-weight: 500; line-height: 1.12; letter-spacing: -0.5px; }

  .locations { position: absolute; left: 63px; top: 1038px; list-style: none; }
  .locations li { display: flex; align-items: center; height: 22px; margin-bottom: 30px; color: var(--white); font-size: 19px; font-weight: 500; letter-spacing: -0.4px; }
  .locations li::before { content: ""; width: 22px; height: 22px; border-radius: 50%; background: var(--red); margin-right: 14px; flex: none; }

  .contact-call { position: absolute; left: 433px; top: 1030px; width: 404px; text-align: center; color: var(--green); font-size: 36px; font-weight: 600; line-height: 1.1; letter-spacing: -0.5px; }
  .contact-phone { position: absolute; left: 433px; top: 1086px; width: 404px; text-align: center; color: var(--red); font-size: 48px; font-weight: 500; line-height: 1.1; letter-spacing: -1px; }
</style>
</head>
<body>
<main class="flyer">
  <div class="panel-top"></div>
  <div class="band"></div>
  <div class="panel-bottom"></div>

  <div class="photo" role="img" aria-label="Smiling businesswoman in a black suit holding a fan of hundred-dollar bills and giving a thumbs up"></div>

  <h1 class="headline">
    <span class="hl-sameday">Same Day</span>
    <span class="hl-tax">Tax</span>
    <span class="hl-advance">Advance</span>
    <span class="hl-upto">up to</span>
    <span class="hl-amount">$6,000</span>
  </h1>

  <div class="brand">
    <span class="brand-dot"></span>
    <span class="brand-name">Harbrook Financial Group</span>
  </div>

  <p class="band-lead">File your taxes and apply for an</p>
  <h2 class="band-title">Easy Advance</h2>

  <section class="feature feature-1">
    <svg width="104" height="60" viewBox="0 0 104 60" aria-hidden="true">
      <circle cx="28" cy="30" r="24" fill="none" stroke="var(--green)" stroke-width="7"/>
      <circle cx="76" cy="30" r="24" fill="none" stroke="var(--green)" stroke-width="7"/>
      <rect x="46" y="10" width="12" height="40" fill="var(--white)"/>
      <path d="M44 48 L60 12" stroke="var(--green)" stroke-width="6" stroke-linecap="round"/>
      <text x="28" y="38" text-anchor="middle" font-family="Oswald, sans-serif" font-weight="600" font-size="20" fill="var(--red)">24</text>
      <text x="78" y="38" text-anchor="middle" font-family="Oswald, sans-serif" font-weight="600" font-size="20" fill="var(--red)">7</text>
    </svg>
    <p>Available in 24<br>Hours or less</p>
  </section>

  <section class="feature feature-2">
    <svg width="64" height="64" viewBox="0 0 64 64" aria-hidden="true">
      <circle cx="32" cy="32" r="27" fill="none" stroke="var(--green)" stroke-width="7"/>
      <text x="32" y="44" text-anchor="middle" font-family="Oswald, sans-serif" font-weight="600" font-size="34" fill="var(--red)">$</text>
    </svg>
    <p>Choose your<br>Loan Amount</p>
  </section>

  <section class="feature feature-3">
    <svg width="64" height="64" viewBox="0 0 64 64" aria-hidden="true">
      <path d="M52 18 A26 26 0 1 0 58 32" fill="none" stroke="var(--green)" stroke-width="7" stroke-linecap="round"/>
      <path d="M14 32 h5 M45 32 h5 M32 50 v-5" stroke="var(--green)" stroke-width="3"/>
      <path d="M21 28 L31 38 L55 10" fill="none" stroke="var(--red)" stroke-width="7" stroke-linecap="round" stroke-linejoin="round"/>
    </svg>
    <p>Quick and<br>Easy</p>
  </section>

  <ul class="locations">
    <li>Address XXXXX XXX XXX</li>
    <li>Address XXXXX XXX XXX</li>
    <li>Address XXXXX XXX XXX</li>
  </ul>

  <p class="contact-call">Contact Us Today!</p>
  <p class="contact-phone">(000) 123 4567 890</p>
</main>
</body>
</html>
```